Tinker's Lamp sports bar beer & food menu

We need a menu design for our gastropub sports bar in L.A.'s Sawtelle Neighborhood (Little Osaka). We have a full-bar (hard liquor, craft beer, wine and cocktails) . We have a lunch and dinner menu as well as a happy hour menu. On Sundays we have a seperate menu with brunch items. The design concept is a British pub type of sports bar. We're looking for something different from our existing menu design. Ideally something cleaner and more legible. It should mesh a simple, modern sensibility with the more traditional darkened pub style of our interior design.

You can check out our Voxly page for photos of the interior/exterior:
https://www.reviewhatch.example/biz_photos/tinkers-lamp-los-angeles?tab=interior

You can view our existing menu here:
https://www.reviewhatch.example/biz_photos/tinkers-lamp-los-angeles?tab=menu

If there's an area of the design that can be a little more playful it's our highlighted event schedule so that the events will stand out.

Target Market(s)

Age of 25 and up. Sawtelle is a cultural hub that caters to a younger, moderately affluent crowd.

Industry/Entity Type

Sports Bar

Font styles to use
Sans Serif

Colors

Designer to choose colors to be used in the design.

Requirements
Must have
• Logo, highlighted event schedule (beer pong Monday, trivia Tuesday, taco Tuesday, whiskey Wednesday, karaoke Saturday). The menu should be easy to read in a darkened bar. We'll be printing on standard 8.5x11 in portrait.
Nice to have
• We're trying to have the menu take up as few pages as possible.
Should not have
• We're trying to have the menu take up as few pages as possible. Food photography isn't necessary. A cover isn't necessary. Please avoid clip art of food.

```html
<!DOCTYPE html>
<html lang="en">
<head>
<meta charset="utf-8">
<title>Tinker's Lamp — Food &amp; Drink Menu</title>
<link rel="stylesheet" href="https://fonts.googleapis.com/css2?family=Montserrat:wght@400;500;600;700&display=swap">
<style>
  :root {
    --page-bg: #e9e6e1;
    --card-white: #ffffff;
    --band-gold: #e9b73c;
    --band-gold-deep: #dca82c;
    --brick-dark: #2a2826;
    --brick-light: #77716a;
    --ink: #161412;
    --ink-soft: #55504a;
    --rule: #d9d3c8;
    --card-shadow: rgba(0, 0, 0, 0.18);
  }
  * { margin: 0; padding: 0; box-sizing: border-box; }
  html, body {
    width: 1200px;
    height: 906px;
    overflow: hidden;
    background: var(--page-bg);
    font-family: "Montserrat", sans-serif;
    color: var(--ink);
  }
  .canvas {
    width: 1200px;
    height: 906px;
    display: flex;
    align-items: center;
    justify-content: center;
  }
  .menu-page {
    width: 660px;
    height: 866px;
    background: var(--card-white);
    box-shadow: 0 10px 30px var(--card-shadow);
    display: flex;
    flex-direction: column;
    overflow: hidden;
  }

  /* Header band */
  .menu-header { position: relative; height: 232px; flex: none; }
  .menu-header svg { display: block; }
  .band-gold { fill: url(#goldBand); }
  .brick-photo { fill: url(#brickTone); }
  .panel-white { fill: var(--card-white); }
  .brand-lockup {
    position: absolute;
    left: 40px;
    bottom: 20px;
    display: flex;
    align-items: center;
    gap: 14px;
  }
  .brand-mark { width: 38px; height: 38px; background: var(--band-gold); flex: none; }
  .brand-name { font-size: 38px; font-weight: 600; line-height: 1; letter-spacing: 0.01em; }
  .brand-tagline {
    font-size: 11px;
    font-weight: 500;
    letter-spacing: 0.5em;
    margin-top: 6px;
    color: var(--ink-soft);
  }

  /* Event schedule */
  .event-schedule {
    margin: 4px 40px 0;
    background: var(--brick-dark);
    border-radius: 6px;
    padding: 14px 16px 16px;
    flex: none;
  }
  .event-schedule h2 {
    font-size: 13px;
    font-weight: 700;
    letter-spacing: 0.3em;
    color: var(--band-gold);
    text-align: center;
    margin-bottom: 10px;
  }
  .event-list { display: grid; grid-template-columns: repeat(4, 1fr); gap: 8px; list-style: none; }
  .event-item {
    background: var(--band-gold);
    border-radius: 4px;
    padding: 8px 6px;
    text-align: center;
  }
  .event-day { font-size: 11px; font-weight: 700; letter-spacing: 0.2em; }
  .event-name { font-size: 13px; font-weight: 600; margin-top: 3px; line-height: 1.25; }

  /* Menu columns */
  .menu-body {
    display: grid;
    grid-template-columns: 1fr 1fr;
    gap: 0 36px;
    padding: 20px 40px 0;
    flex: 1;
  }
  .menu-section { margin-bottom: 16px; }
  .menu-section h3 {
    font-size: 15px;
    font-weight: 700;
    letter-spacing: 0.22em;
    padding-bottom: 5px;
    border-bottom: 3px solid var(--band-gold);
    margin-bottom: 8px;
  }
  .menu-item { margin-bottom: 8px; }
  .item-line {
    display: flex;
    justify-content: space-between;
    font-size: 14px;
    font-weight: 600;
  }
  .item-desc { font-size: 12px; color: var(--ink-soft); margin-top: 1px; }

  /* Footer notes */
  .menu-footer {
    flex: none;
    margin: 0 40px 22px;
    padding-top: 10px;
    border-top: 1px solid var(--rule);
    display: flex;
    justify-content: space-between;
    font-size: 12px;
    font-weight: 500;
  }
  .menu-footer strong { font-weight: 700; color: var(--ink); }
</style>
</head>
<body>
  <main class="canvas">
    <article class="menu-page" aria-label="Tinker's Lamp food and drink menu">

      <header class="menu-header">
        <svg width="660" height="232" viewBox="0 0 660 232" xmlns="http://www.w3.org/2000/svg">
          <defs>
            <linearGradient id="goldBand" x1="0" y1="1" x2="1" y2="0">
              <stop offset="0" stop-color="var(--band-gold)"/>
              <stop offset="1" stop-color="var(--band-gold-deep)"/>
            </linearGradient>
            <linearGradient id="brickTone" x1="0" y1="0" x2="1" y2="1">
              <stop offset="0" stop-color="var(--brick-light)"/>
              <stop offset="0.6" stop-color="var(--brick-dark)"/>
              <stop offset="1" stop-color="#1b1a19"/>
            </linearGradient>
          </defs>
          <rect class="band-gold" x="0" y="0" width="660" height="232"/>
          <path class="brick-photo" role="img" aria-label="Photograph of a dark weathered brick wall"
                d="M0,0 L660,0 L660,40 C 480,72 250,80 0,112 Z"/>
          <path class="panel-white" d="M0,232 L0,190 C 200,140 420,118 660,112 L660,232 Z"/>
        </svg>
        <div class="brand-lockup">
          <span class="brand-mark" aria-hidden="true"></span>
          <div>
            <div class="brand-name">Tinker's Lamp</div>
            <div class="brand-tagline">PUB &amp; RESTAURANT</div>
          </div>
        </div>
      </header>

      <section class="event-schedule">
        <h2>THIS WEEK AT THE PUB</h2>
        <ul class="event-list">
          <li class="event-item"><div class="event-day">MON</div><div class="event-name">Beer Pong</div></li>
          <li class="event-item"><div class="event-day">TUE</div><div class="event-name">Trivia &amp; Tacos</div></li>
          <li class="event-item"><div class="event-day">WED</div><div class="event-name">Whiskey Night</div></li>
          <li class="event-item"><div class="event-day">SAT</div><div class="event-name">Karaoke</div></li>
        </ul>
      </section>

      <div class="menu-body">
        <div class="menu-column">
          <section class="menu-section">
            <h3>STARTERS</h3>
            <div class="menu-item"><div class="item-line"><span>Scotch Egg</span><span>9</span></div><p class="item-desc">Soft egg, pork sausage, mustard</p></div>
            <div class="menu-item"><div class="item-line"><span>Fish Bites</span><span>11</span></div><p class="item-desc">Beer batter, tartare sauce</p></div>
            <div class="menu-item"><div class="item-line"><span>Loaded Chips</span><span>10</span></div><p class="item-desc">Cheddar, bacon, spring onion</p></div>
          </section>
          <section class="menu-section">
            <h3>MAINS</h3>
            <div class="menu-item"><div class="item-line"><span>Fish &amp; Chips</span><span>18</span></div><p class="item-desc">Cod, mushy peas, lemon</p></div>
            <div class="menu-item"><div class="item-line"><span>Pub Burger</span><span>16</span></div><p class="item-desc">Aged beef, pickles, brioche</p></div>
            <div class="menu-item"><div class="item-line"><span>Bangers &amp; Mash</span><span>17</span></div><p class="item-desc">Onion gravy, buttery mash</p></div>
          </section>
        </div>
        <div class="menu-column">
          <section class="menu-section">
            <h3>ON TAP</h3>
            <div class="menu-item"><div class="item-line"><span>House Lager</span><span>7</span></div><p class="item-desc">Crisp, light, pint or half</p></div>
            <div class="menu-item"><div class="item-line"><span>West Coast IPA</span><span>8</span></div><p class="item-desc">Pine, citrus, bold hops</p></div>
            <div class="menu-item"><div class="item-line"><span>Irish Stout</span><span>8</span></div><p class="item-desc">Roasted, creamy, smooth</p></div>
          </section>
          <section class="menu-section">
            <h3>COCKTAILS</h3>
            <div class="menu-item"><div class="item-line"><span>Gin Fizz</span><span>12</span></div><p class="item-desc">Gin, lemon, soda</p></div>
            <div class="menu-item"><div class="item-line"><span>Old Fashioned</span><span>13</span></div><p class="item-desc">Bourbon, bitters, orange</p></div>
            <div class="menu-item"><div class="item-line"><span>Moscow Mule</span><span>12</span></div><p class="item-desc">Vodka, ginger beer, lime</p></div>
          </section>
        </div>
      </div>

      <footer class="menu-footer">
        <span><strong>Happy Hour</strong> Mon–Fri 3–6pm</span>
        <span><strong>Sunday Brunch</strong> 10am–3pm</span>
      </footer>
    </article>
  </main>
</body>
</html>
```